National Mission Critical Construction Contractor needs Stationery Design to make a bold statement

We are a small commercial construction company, working primarily in mission critical facilities across the U.S.. We have exciting corporate changes going an and a new logo and office space so we need new stationery. The final design should incorporate our new logo and invoke a fresh, high-tech feel while looking simple and modern.

Industry/Entity Type

Construction

Contact Information for Business Card

We are required to list our state licensing qualifications on the back of our card.

Font styles to use
Sans Serif

Requirements
Must have
• We need to have a design for second page of stationery, envelopes both standard and with a window and for a 3 x 4 notepad.

```html
<!DOCTYPE html>
<html lang="en">
<head>
<meta charset="utf-8">
<title>Stonebridge Stationery</title>
<link href="https://fonts.googleapis.com/css2?family=Source+Sans+3:wght@400;600&display=swap" rel="stylesheet">
<style>
:root{
  --backdrop:#a9a9a9;
  --paper:#f4f3f1;
  --white:#ffffff;
  --brand-blue:#0f6fba;
  --sky-blue:#3aa6dc;
  --mid-blue:#2a7fc4;
  --leaf-green:#8cc43f;
  --ink:#4d4d4d;
  --ink-soft:#5a5a5a;
  --watermark:#dbe6ef;
  --signature-tint:#d6d5d3;
}
*{margin:0;padding:0;box-sizing:border-box}
html,body{width:1200px;height:753px;overflow:hidden}
body{background:var(--backdrop);font-family:"Source Sans 3",sans-serif;color:var(--ink);position:relative}
.sheet{position:absolute;box-shadow:0 1px 4px rgba(0,0,0,.25)}
.brand{display:flex;align-items:center;gap:6px}
.brand-dot{border:2px solid var(--brand-blue);border-radius:50%}
.brand-name{color:var(--brand-blue);font-weight:400;letter-spacing:.02em}
.icon{width:7px;height:7px;fill:currentColor;flex:none}

/* Letterhead */
.letterhead{left:36px;top:31px;width:490px;height:691px;background:var(--paper);overflow:hidden}
.letterhead .brand{position:absolute;left:48px;top:54px}
.letterhead .brand-dot{width:30px;height:30px}
.letterhead .brand-name{font-size:17px}
.letterhead .watermark{position:absolute;left:51px;top:220px;width:356px;height:356px;border:16px solid var(--watermark);border-radius:50%;opacity:.7}
.letterhead .contact{position:absolute;left:344px;top:45px;font-size:8.3px;line-height:11px;color:var(--ink-soft)}
.contact-list{list-style:none;margin-top:4px}
.contact-list li{display:flex;align-items:center;gap:5px;color:var(--brand-blue)}
.contact-list li span{color:var(--ink-soft)}
.letter{position:absolute;left:49px;top:194px;width:396px}
.salutation{font-size:13px;margin-bottom:27px}
.letter p{font-size:7.1px;line-height:11.7px;margin-bottom:11.7px;text-align:justify;color:var(--ink-soft)}
.signoff{position:absolute;left:49px;top:482px;font-size:7.4px;color:var(--ink-soft)}
.signature{width:64px;height:20px;margin:8px 0 8px;background:var(--signature-tint);border-radius:2px}
.signer{margin-left:3px;line-height:13px}
.footer{position:absolute;left:0;bottom:0;display:block}
.footer-url{position:absolute;right:34px;bottom:10px;font-size:8px;letter-spacing:.28em;color:var(--white)}

/* Business cards */
.card{width:214px;height:122px;overflow:hidden}
.card-front{left:649px;top:177px;background:var(--white)}
.card-front .brand{position:absolute;left:12px;top:14px;gap:4px}
.card-front .brand-dot{width:22px;height:22px}
.card-front .brand-name{font-size:11px}
.card-front svg{position:absolute;left:0;top:52px}
.card-details{position:absolute;left:12px;top:74px;list-style:none;font-size:5.4px;line-height:8.2px;color:var(--white)}
.card-details li{display:flex;align-items:center;gap:4px}
.card-details .icon{width:5px;height:5px}
.card-person{position:absolute;right:11px;top:66px;text-align:right;color:var(--white)}
.card-person .name{font-size:7.6px;font-weight:600}
.card-person .role{font-size:5.6px}
.card-person .addr{font-size:5.4px;line-height:7.5px;margin-top:16px}
.card-back{left:895px;top:178px;background:var(--white)}
.card-back .pattern{position:absolute;inset:0;background:linear-gradient(135deg,#eef4f9,#dfeaf3)}
.card-back .brand-dot{position:absolute;left:163px;top:77px;width:24px;height:24px;background:var(--white)}
.card-back .url{position:absolute;right:13px;bottom:13px;font-size:5.2px;color:var(--ink-soft)}

/* Envelopes */
.envelope-back{left:615px;top:360px;width:550px;height:250px;background:var(--white)}
.envelope-back svg{position:absolute;left:0;top:0}
.envelope-back .brand-dot{position:absolute;left:258px;top:26px;width:34px;height:34px;border-color:var(--white)}
.envelope-back .url{position:absolute;left:0;width:100%;top:63px;text-align:center;font-size:8.2px;color:var(--white)}
.envelope-front{left:547px;top:470px;width:550px;height:252px;background:var(--paper);overflow:hidden}
.envelope-front .watermark{position:absolute;left:300px;top:6px;width:250px;height:250px;border:14px solid var(--watermark);border-radius:50%;opacity:.8}
.envelope-front .brand{position:absolute;left:25px;top:24px}
.envelope-front .brand-dot{width:30px;height:30px}
.envelope-front .brand-name{font-size:14px}
.envelope-front address{position:absolute;left:26px;top:84px;font-style:normal;font-size:8.6px;line-height:11.8px;color:var(--ink-soft)}
</style>
</head>
<body>

<section class="sheet letterhead">
  <div class="watermark"></div>
  <div class="brand"><span class="brand-dot"></span><span class="brand-name">STONEBRIDGE</span></div>
  <div class="contact">
    <div>1420 Harbor View Road<br>Juneau, Alaska 99801</div>
    <ul class="contact-list">
      <li><svg class="icon" viewBox="0 0 10 10"><path d="M2 0h2l1 3-1.5 1a6 6 0 0 0 2.5 2.5L7 5l3 1v2a2 2 0 0 1-2 2A8 8 0 0 1 0 2a2 2 0 0 1 2-2z"/></svg><span>555 210 4471</span></li>
      <li><svg class="icon" viewBox="0 0 10 10"><path d="M2.5 0h5v10h-5zM3.5 1v7h3V1z"/></svg><span>555 382 9016</span></li>
      <li><svg class="icon" viewBox="0 0 10 10"><path d="M2 0h6v3H2zM0 3h10v5H8v2H2V8H0zM3 6v3h4V6z"/></svg><span>555 647 2203</span></li>
      <li><svg class="icon" viewBox="0 0 10 10"><path d="M0 2h10v6H0zM1 3l4 3 4-3z"/></svg><span>info@stonebridgecm.com</span></li>
    </ul>
  </div>
  <div class="letter">
    <div class="salutation">Dear Mr. Carter,</div>
    <p>Lorem ipsum dolor sit amet, consectetur adipiscing elit. Donec orci purus, luctus vitae dignissim eu, iaculis sed purus. Vivamus faucibus, ipsum nec aliquet viverra, leo mauris condimentum ligula, sit amet sagittis enim ligula quis arcu. Nam egestas tortor id nisi porttitor mattis. In tortor ante, ultricies in suscipit a, tempus non massa. Vivamus et auctor mi. Fusce vel massa nulla. Phasellus nec eros mauris, et scelerisque orci.</p>
    <p>Donec malesuada orci vitae nulla accumsan porta a id massa. Quisque accumsan iaculis magna sit amet fringilla. Maecenas consequat, magna eget tincidunt semper, odio nibh rutrum mi, id feugiat ante nisi eu risus. Vestibulum nunc orci, rhoncus a placerat in, ultricies in mi. Cras mattis varius eros, vel fringilla nisi suscipit eget. Quisque scelerisque sagittis nulla at porttitor.</p>
    <p>Sed id augue vitae urna euismod commodo aliquet a quam. Pellentesque arcu velit, cursus et malesuada ut, consequat et diam. Nullam erat sem, rhoncus id ullamcorper vitae, rhoncus et arcu. In ultricies ultricies nulla, ut rutrum nisi iaculis at. Donec eu magna a metus ornare faucibus. Fusce aliquet faucibus ultricies. Morbi semper, est id tincidunt gravida, sem arcu adipiscing lacus, ac bibendum nulla leo eu purus. Quisque nec diam sed risus consectetur a accumsan quis quis nibh. Vestibulum id purus lorem.</p>
    <p>It is a long established fact that a reader will be distracted by the readable content of a page when looking at its layout. The point of using Lorem Ipsum is that it has a more-or-less normal distribution of letters, as opposed to using 'Content here, content here', making it look like readable English. Many desktop publishing packages</p>
  </div>
  <div class="signoff">
    <div>Sincerely,</div>
    <div class="signature" role="img" aria-label="Handwritten signature of Daniel Reeves"></div>
    <div class="signer">Daniel Reeves<br>CEO/ Founder</div>
  </div>
  <svg class="footer" width="490" height="31" viewBox="0 0 490 31">
    <polygon points="0,11 103,11 100,17 0,17" fill="var(--leaf-green)"/>
    <polygon points="106,11 205,11 202,17 103,17" fill="var(--sky-blue)"/>
    <polygon points="208,11 306,11 303,17 205,17" fill="var(--mid-blue)"/>
    <polygon points="320,0 490,0 490,31 0,31 0,22 300,22" fill="var(--brand-blue)"/>
  </svg>
  <div class="footer-url">www.stonebridgecm.com</div>
</section>

<section class="sheet card card-front">
  <div class="brand"><span class="brand-dot"></span><span class="brand-name">STONEBRIDGE</span></div>
  <svg width="214" height="70" viewBox="0 0 214 70">
    <polygon points="0,11 38,11 36,15 0,15" fill="var(--leaf-green)"/>
    <polygon points="40,11 76,11 74,15 38,15" fill="var(--sky-blue)"/>
    <polygon points="78,11 114,11 112,15 76,15" fill="var(--mid-blue)"/>
    <polygon points="125,0 214,0 214,70 0,70 0,17 112,17" fill="var(--brand-blue)"/>
  </svg>
  <ul class="card-details">
    <li><svg class="icon" viewBox="0 0 10 10"><path d="M2 0h2l1 3-1.5 1a6 6 0 0 0 2.5 2.5L7 5l3 1v2a2 2 0 0 1-2 2A8 8 0 0 1 0 2a2 2 0 0 1 2-2z"/></svg>555 210 4471</li>
    <li><svg class="icon" viewBox="0 0 10 10"><path d="M2.5 0h5v10h-5zM3.5 1v7h3V1z"/></svg>555 382 9016</li>
    <li><svg class="icon" viewBox="0 0 10 10"><path d="M2 0h6v3H2zM0 3h10v5H8v2H2V8H0zM3 6v3h4V6z"/></svg>555 647 2203</li>
    <li><svg class="icon" viewBox="0 0 10 10"><path d="M0 2h10v6H0zM1 3l4 3 4-3z"/></svg>info@stonebridgecm.com</li>
    <li><svg class="icon" viewBox="0 0 10 10"><circle cx="5" cy="5" r="5"/></svg>www.stonebridgecm.com</li>
  </ul>
  <div class="card-person">
    <div class="name">DANIEL REEVES</div>
    <div class="role">CEO/Founder</div>
    <div class="addr">1420 Harbor View Road<br>Juneau, Alaska 99801</div>
  </div>
</section>

<section class="sheet card card-back">
  <div class="pattern" role="img" aria-label="Light blue repeating brand pattern"></div>
  <span class="brand-dot"></span>
  <div class="url">www.stonebridgecm.com</div>
</section>

<section class="sheet envelope-back">
  <svg width="550" height="250" viewBox="0 0 550 250">
    <path d="M0 0H550L541 72Q538 91 518 91H32Q12 91 9 72Z" fill="var(--brand-blue)"/>
  </svg>
  <span class="brand-dot"></span>
  <div class="url">www.stonebridgecm.com</div>
</section>

<section class="sheet envelope-front">
  <div class="watermark"></div>
  <div class="brand"><span class="brand-dot"></span><span class="brand-name">STONEBRIDGE</span></div>
  <address>1420 Harbor View Road<br>Juneau, Alaska 99801</address>
  <svg class="footer" width="550" height="31" viewBox="0 0 550 31">
    <polygon points="0,11 122,11 119,17 0,17" fill="var(--leaf-green)"/>
    <polygon points="125,11 246,11 243,17 122,17" fill="var(--sky-blue)"/>
    <polygon points="249,11 369,11 366,17 246,17" fill="var(--mid-blue)"/>
    <polygon points="383,0 550,0 550,31 0,31 0,22 363,22" fill="var(--brand-blue)"/>
  </svg>
  <div class="footer-url">www.stonebridgecm.com</div>
</section>

</body>
</html>
```